Verodex business card

Business card for sustainable investment company called "Verodex". Verodex is an exchange platform selling carbon credits between buyers and sellers. Carbon Credits are an environmental commodity for reducing global carbon emissions.

the card should obviously have our logo and the theme should be sustainability/environment mixed with a trading platform.

Contact Information for Business Card

Logo, Name, Title, Phone, Email

Colors
0054AA
0677BA
7BADD7
CADEEF
E8F1F8
0094D4
00A9DD
6FCCEA
C7EBF8
E9F6FB
00AB8E
00BBA5
67D7C9
C6EFE9
E9F9F6
59FF00
82FF00
B8FF75
E3FFCB
F4FFEA

```html
<!DOCTYPE html>
<html lang="en">
<head>
<meta charset="UTF-8">
<title>Verodex Business Card</title>
<link href="https://fonts.googleapis.com/css2?family=Poppins:wght@400;500;600&display=swap" rel="stylesheet">
<style>
  :root {
    --backdrop: #e4e4e4;
    --card-front: #f7f7f8;
    --navy-top: #13345f;
    --navy-bottom: #0a254f;
    --ink: #1f2d45;
    --text: #2b3446;
    --accent: #2aa7e3;
    --accent-deep: #1f7fdc;
    --divider: #b9bcc2;
  }
  * { margin: 0; padding: 0; box-sizing: border-box; }
  html, body {
    width: 1200px; height: 1200px; overflow: hidden;
    background: var(--backdrop);
    font-family: "Poppins", sans-serif;
  }
  .canvas { position: relative; width: 1200px; height: 1200px; }
  .card {
    position: absolute; left: 257px; width: 686px; height: 392px;
    border-radius: 22px; overflow: hidden;
  }
  .card-front { top: 165px; background: var(--card-front); }
  .card-back {
    top: 653px;
    background: linear-gradient(180deg, var(--navy-top), var(--navy-bottom));
    display: flex; align-items: center; justify-content: center;
  }
  .brand {
    position: absolute; left: 68px; top: 180px;
    display: flex; align-items: center; gap: 14px;
  }
  .brand-dot {
    width: 34px; height: 34px; border-radius: 50%;
    background: var(--accent-deep);
  }
  .brand-name {
    font-weight: 600; font-size: 36px; letter-spacing: 0.5px;
    color: var(--ink); line-height: 1;
  }
  .divider {
    position: absolute; left: 361px; top: 87px;
    width: 1.5px; height: 215px; background: var(--divider);
  }
  .details { position: absolute; left: 384px; top: 96px; color: var(--text); }
  .person-name {
    font-weight: 600; font-size: 23px; color: var(--accent);
    letter-spacing: 0.3px; line-height: 1.2;
  }
  .person-title { font-size: 15.5px; line-height: 1.3; }
  .address { margin-top: 12px; font-size: 16.5px; line-height: 1.3; }
  .contacts { list-style: none; margin-top: 10px; font-size: 17px; }
  .contacts li { display: flex; align-items: center; gap: 9px; line-height: 20.5px; }
  .contacts svg { width: 14px; height: 14px; flex: none; fill: var(--accent-deep); }
  .back-brand {
    display: flex; align-items: center; gap: 22px;
  }
  .back-brand .brand-dot { width: 58px; height: 58px; background: #2ec0e8; }
  .back-brand .brand-name { font-size: 64px; color: #2ec0e8; }
</style>
</head>
<body>
<main class="canvas">
  <section class="card card-front">
    <div class="brand">
      <span class="brand-dot"></span>
      <span class="brand-name">VERODEX</span>
    </div>
    <div class="divider"></div>
    <div class="details">
      <h1 class="person-name">DANIEL MORROW</h1>
      <p class="person-title">Managing Director</p>
      <p class="address">4120 Juniper Court<br>Portland, Oregon 97205</p>
      <ul class="contacts">
        <li>
          <svg viewBox="0 0 24 24"><path d="M6.6 10.8a15.1 15.1 0 0 0 6.6 6.6l2.2-2.2c.3-.3.7-.4 1-.2 1.1.4 2.3.6 3.6.6.6 0 1 .4 1 1V20c0 .6-.4 1-1 1A17 17 0 0 1 3 4c0-.6.4-1 1-1h3.5c.6 0 1 .4 1 1 0 1.3.2 2.5.6 3.6.1.3 0 .7-.2 1z"/></svg>
          503-218-4470
        </li>
        <li>
          <svg viewBox="0 0 24 24"><path d="M7 1h10a2 2 0 0 1 2 2v18a2 2 0 0 1-2 2H7a2 2 0 0 1-2-2V3a2 2 0 0 1 2-2zm0 3v14h10V4zm5 15.5a1.2 1.2 0 1 0 0 2.4 1.2 1.2 0 0 0 0-2.4z"/></svg>
          503-691-2358
        </li>
        <li>
          <svg viewBox="0 0 24 24"><path d="M2 5h20v14H2zm2 2v.5l8 5.5 8-5.5V7zm0 3v7h16v-7l-8 5.5z"/></svg>
          hello@verodex.com
        </li>
        <li>
          <svg viewBox="0 0 24 24"><path d="M12 2a10 10 0 1 0 0 20 10 10 0 0 0 0-20zm-1 17.9A8 8 0 0 1 4.2 10.6L9 15.4v1a2 2 0 0 0 2 2zm6.9-2.5A2 2 0 0 0 16 16h-1v-3a1 1 0 0 0-1-1H8v-2h2a1 1 0 0 0 1-1V7h2a2 2 0 0 0 2-2v-.4a8 8 0 0 1 2.9 12.8z"/></svg>
          www.verodex.com
        </li>
      </ul>
    </div>
  </section>

  <section class="card card-back">
    <div class="back-brand">
      <span class="brand-dot"></span>
      <span class="brand-name">VERODEX</span>
    </div>
  </section>
</main>
</body>
</html>
```